Photography Business, Business Card

Looking for a unique cutting edge card that takes advantage of the latest printing technologies. Please review this site for all the options they office: https://glowprintly.com. If you can think it they can do it. And if you have an idea and do not know if they can do it, I will check into it.

Target Market(s)

People and places I took images of and future clients.

Industry/Entity Type

Photography

Contact Information for Business Card

Name, cell & email. Derek Holloway, dholloway@kpnvisuals.com, 312-748-2961

Colors

Designer to choose only greyscale colors for use in the design.

Requirements
Must have
• 100% cutting edge. Is so great, those I hand it to always show it to someone else. A piece of art.
Nice to have
• Blacks, silvers, greys, some red. Maybe other colors?

```html
<!DOCTYPE html>
<html lang="en">
<head>
<meta charset="utf-8">
<title>Halvane – Business Card</title>
<link rel="stylesheet" href="https://fonts.googleapis.com/css2?family=Poppins:wght@400;500;600&display=swap">
<style>
  :root {
    --stage: #1c1d1f;
    --card-light: #d4d6d9;
    --card-mid: #b4b7bb;
    --card-dark: #9a9da1;
    --ink: #4a4d52;
    --ink-soft: #6c7075;
    --mark: #f1f2f3;
    --mark-dark: #5d6166;
  }
  * { margin: 0; padding: 0; box-sizing: border-box; }
  html, body { width: 1200px; height: 800px; overflow: hidden; }
  body {
    background: var(--stage);
    font-family: "Poppins", sans-serif;
    display: flex;
    align-items: center;
    justify-content: center;
    gap: 60px;
  }
  .card {
    position: relative;
    width: 525px;
    height: 300px;
    border-radius: 22px;
    overflow: hidden;
    background: linear-gradient(135deg, var(--card-light) 0%, var(--card-mid) 55%, var(--card-dark) 100%);
  }
  .card__circle {
    position: absolute;
    border-radius: 50%;
  }
  .card--front .card__circle {
    width: 300px; height: 300px;
    left: -150px; top: 0;
    background: var(--mark-dark);
  }
  .card--front .brand {
    position: absolute;
    left: 180px; top: 114px;
    font-size: 60px;
    font-weight: 500;
    letter-spacing: 3px;
    color: var(--ink);
    line-height: 1;
    white-space: nowrap;
  }
  .card--back .card__circle {
    width: 260px; height: 260px;
    right: 30px; top: -130px;
    background: var(--mark);
  }
  .card--back .brand {
    position: absolute;
    left: 34px; top: 40px;
    font-size: 32px;
    font-weight: 500;
    letter-spacing: 2px;
    color: var(--ink);
    line-height: 1;
    white-space: nowrap;
  }
  .owner {
    position: absolute;
    left: 34px; top: 112px;
    color: var(--ink);
  }
  .owner__name {
    font-size: 30px;
    font-weight: 400;
    line-height: 1.1;
    white-space: nowrap;
  }
  .owner__role {
    font-size: 11px;
    font-weight: 500;
    letter-spacing: 4px;
    color: var(--ink-soft);
    margin-top: 4px;
  }
  .contact {
    position: absolute;
    left: 34px; bottom: 30px;
    font-size: 19px;
    font-weight: 600;
    color: var(--ink);
    line-height: 1.45;
    white-space: nowrap;
  }
</style>
</head>
<body>
  <section class="card card--front" aria-label="Card front">
    <div class="card__circle"></div>
    <div class="brand">Halvane</div>
  </section>

  <section class="card card--back" aria-label="Card back">
    <div class="card__circle"></div>
    <div class="brand">Halvane</div>
    <div class="owner">
      <p class="owner__name">Derek Holloway</p>
      <p class="owner__role">PHOTOGRAPHY</p>
    </div>
    <div class="contact">
      <p class="contact__phone">312-748-2961</p>
      <p class="contact__email">dholloway@kpnvisuals.com</p>
    </div>
  </section>
</body>
</html>
```